GJ & DW Fencing Pty Ltd

We already have an existing logo created by Pixel Harbour however we have restructured to a company. We would like someone to add Pty Ltd to our business name please.

Colors

Designer to choose only greyscale colors for use in the design.

```html
<!DOCTYPE html>
<html lang="en">
<head>
<meta charset="utf-8">
<title>GJ &amp; DW Fencing Pty Ltd – Business Card</title>
<link rel="stylesheet" href="https://fonts.googleapis.com/css2?family=PT+Serif:wght@700&family=Lato:wght@400&display=swap">
<style>
  :root {
    --backdrop: #2b2b2b;
    --card-light: #ffffff;
    --card-dark: #000000;
    --ink: #111111;
    --ink-reverse: #ffffff;
    --rule: #9a9a9a;
  }
  * { margin: 0; padding: 0; box-sizing: border-box; }
  html, body {
    width: 1200px; height: 1200px; overflow: hidden;
    background: var(--backdrop);
  }
  .canvas { position: relative; width: 1200px; height: 1200px; }
  .card {
    position: absolute; top: 310px;
    box-shadow: 0 2px 6px rgba(0,0,0,.45);
  }
  .card--front { left: 234px; width: 364px; height: 593px; background: var(--card-light); color: var(--ink); }
  .card--back  { left: 627px; width: 369px; height: 595px; background: var(--card-dark); color: var(--ink-reverse); }

  .brand {
    position: absolute; left: 0; right: 0;
    font-family: "PT Serif", Georgia, serif; font-weight: 700;
    text-align: center; line-height: 1;
  }
  .brand__initials { display: block; font-size: 50px; letter-spacing: 1px; }
  .brand__trade { display: block; font-size: 24px; letter-spacing: 1px; margin-top: 6px; }
  .brand__entity { display: block; font-size: 11px; letter-spacing: 2px; margin-top: 6px; }
  .card--front .brand { top: 122px; }
  .card--back .brand { top: 232px; }

  .contact-name {
    position: absolute; top: 346px; left: 0; right: 0; text-align: center;
    font-family: "PT Serif", Georgia, serif; font-weight: 700; font-size: 19px; letter-spacing: .5px;
  }
  .contact-item { position: absolute; left: 0; right: 0; text-align: center; }
  .contact-item__marker {
    position: relative; height: 28px;
    display: flex; justify-content: center; align-items: center;
  }
  .contact-item__marker::before,
  .contact-item__marker::after {
    content: ""; position: absolute; top: 50%; width: 50px; height: 1px; background: var(--rule);
  }
  .contact-item__marker::before { left: 119px; }
  .contact-item__marker::after { right: 119px; }
  .contact-item__marker svg { width: 28px; height: 28px; display: block; }
  .contact-item__text {
    font-family: "Lato", Arial, sans-serif; font-size: 17px; margin-top: 3px;
  }
  .contact-item--phone { top: 385px; }
  .contact-item--email { top: 442px; }
  .contact-item--post  { top: 498px; }
  .contact-item--post .contact-item__text { margin-top: 13px; }
</style>
</head>
<body>
<main class="canvas">
  <section class="card card--front">
    <div class="brand">
      <span class="brand__initials">GJ &amp; DW</span>
      <span class="brand__trade">FENCING</span>
      <span class="brand__entity">PTY LTD</span>
    </div>

    <h1 class="contact-name">TOM CARRICK</h1>

    <div class="contact-item contact-item--phone">
      <div class="contact-item__marker">
        <svg viewBox="0 0 28 28" aria-hidden="true">
          <circle cx="14" cy="14" r="14" fill="#000"/>
          <path d="M9 10.5c0-1 .8-1.8 1.8-1.8h6.4c1 0 1.8.8 1.8 1.8v.8h-2.4v-.8h-5.2v.8H9z" fill="#fff"/>
          <rect x="8.5" y="12.5" width="11" height="7" rx="1.2" fill="#fff"/>
          <circle cx="14" cy="16" r="1.8" fill="#000"/>
        </svg>
      </div>
      <p class="contact-item__text">044 7120594</p>
    </div>

    <div class="contact-item contact-item--email">
      <div class="contact-item__marker">
        <svg viewBox="0 0 28 28" aria-hidden="true">
          <circle cx="14" cy="14" r="14" fill="#000"/>
          <rect x="8" y="9.5" width="12" height="9" fill="#fff"/>
          <path d="M8 9.5l6 5 6-5" fill="none" stroke="#000" stroke-width="1.2"/>
        </svg>
      </div>
      <p class="contact-item__text">Gjdwfencing@outlook.com</p>
    </div>

    <div class="contact-item contact-item--post">
      <div class="contact-item__marker">
        <svg viewBox="0 0 28 28" aria-hidden="true">
          <circle cx="14" cy="14" r="14" fill="#000"/>
          <path d="M14 6.5a5 5 0 0 1 5 5c0 3.6-5 9.5-5 9.5s-5-5.9-5-9.5a5 5 0 0 1 5-5z" fill="#fff"/>
          <circle cx="14" cy="11.5" r="2" fill="#000"/>
        </svg>
      </div>
      <p class="contact-item__text">PO Box 418 Ridgeford WA 6520</p>
    </div>
  </section>

  <section class="card card--back">
    <div class="brand">
      <span class="brand__initials">GJ &amp; DW</span>
      <span class="brand__trade">FENCING</span>
      <span class="brand__entity">PTY LTD</span>
    </div>
  </section>
</main>
</body>
</html>
```